IT Services Company Needs Corporate PPT Template

This is urgent (need a fast turn around). We need a corporate PPT template deck (NOTE: Deck should be in 4:3 ratio) for our IT Services firm that is clean but slick and modern. We tend to lean more towards the flat design look. I'm attaching a zip file which includes our Corporate Branding Guide (which is in progress), color scheme, A PPT deck as inspiration (our logo is on the last slide), our font (LATO). Our newly launched website is located at: http://www.veranthix.com.

As an example of a deck we like see: http://slidemorrow.net/item/clean-multipurpose-business-presentation-template/5318206?WT.ac=category_thumb&WT.seg_1=category_thumb&WT.z_author=PixelHarbor
Although we don't want "this" deck - it gives an idea of style.

I'm also attaching a copy of our corporate deck as it is now to give you an idea of the type of content that would appear on various slides. We definitely want the following slides (at least) within the template:

Title Slide
Blank Slide
2 Column - with bullets
2 Column - no bullets
Single Column - no bullets
Single Column - with bullets
Various Charts and Tables (see example deck)
Meet the Team
Offering Slide
Customer Showcase
Timeline
Case Study
Contact US

Note: Being awarded this job will lead to a second job of creating our corporate deck.

Target Market(s)

CIO, CEO, Technology Officers, Sales People, Marketing, IT heads and staff, Customers, Prospective customers

Industry/Entity Type

Business

Requirements
Must have
• See description and attached files

```html
<!DOCTYPE html>
<html lang="en">
<head>
<meta charset="UTF-8">
<title>Veranthix – Agenda</title>
<link rel="stylesheet" href="https://fonts.googleapis.com/css2?family=Lato:wght@400;700;900&family=Rajdhani:wght@500;600&display=swap">
<style>
  :root {
    --header-dark: #08506f;
    --header-mid: #0f6286;
    --accent-teal: #5bbcd6;
    --number-blue: #3399e0;
    --marker-gold: #f2b731;
    --item-text: #3a3d42;
    --panel-white: #ffffff;
    --footer-light: #eeeeee;
    --footer-dark: #dcdcdc;
    --logo-navy: #1d3f74;
    --presenter-blue: #2b8fd3;
  }
  * { margin: 0; padding: 0; box-sizing: border-box; }
  html, body { width: 1200px; height: 900px; overflow: hidden; background: #ffffff; }
  .slide {
    position: relative;
    width: 1200px;
    height: 900px;
    overflow: hidden;
    background: linear-gradient(100deg, #ffffff 45%, #f3f5f7 75%, #eef1f4 100%);
    font-family: 'Lato', sans-serif;
  }
  .slide-header {
    position: absolute; left: 0; top: 0; width: 100%; height: 99px;
    background: linear-gradient(90deg, var(--header-dark), var(--header-mid) 60%, var(--header-dark));
  }
  .project-title {
    position: absolute; left: 33px; top: 26px;
    color: #ffffff; font-weight: 700; font-size: 39px; line-height: 1;
  }
  .section-title {
    position: absolute; left: 32px; top: 152px;
    color: var(--accent-teal); font-weight: 700; font-size: 33px; line-height: 1;
  }
  .agenda-item {
    position: absolute; height: 63px; width: 490px;
    display: flex; align-items: center;
  }
  .agenda-item.right { background: var(--panel-white); width: 491px; }
  .agenda-number {
    width: 70px; height: 63px;
    background: var(--number-blue);
    border-left: 5px solid var(--marker-gold);
    color: #ffffff;
    font-family: 'Rajdhani', sans-serif; font-weight: 500; font-size: 35px;
    display: flex; align-items: center; justify-content: center;
    padding-right: 4px;
  }
  .agenda-label {
    margin-left: 18px;
    font-family: 'Rajdhani', sans-serif; font-weight: 600; font-size: 28px;
    color: var(--item-text);
  }
  .slide-footer {
    position: absolute; left: 0; top: 818px; width: 100%; height: 82px;
    background: linear-gradient(180deg, var(--footer-light), var(--footer-dark));
    box-shadow: 0 -2px 5px rgba(0,0,0,0.12);
  }
  .brand-name {
    position: absolute; left: 24px; top: 22px;
    color: var(--logo-navy); font-weight: 900; font-size: 36px; line-height: 1;
  }
  .presenter {
    position: absolute; right: 17px; top: 30px;
    color: var(--presenter-blue); font-size: 17px; line-height: 1;
    display: flex; align-items: baseline; gap: 6px;
  }
  .presenter-name { font-weight: 700; font-size: 22px; }
</style>
</head>
<body>
<div class="slide">
  <header class="slide-header">
    <h1 class="project-title">Project Title here</h1>
  </header>

  <h2 class="section-title">Agenda Slide</h2>

  <div class="agenda-item" style="left:76px; top:240px;"><span class="agenda-number">01</span><span class="agenda-label">Slide Title Here</span></div>
  <div class="agenda-item" style="left:76px; top:336px;"><span class="agenda-number">02</span><span class="agenda-label">Slide Title Here</span></div>
  <div class="agenda-item" style="left:76px; top:440px;"><span class="agenda-number">03</span><span class="agenda-label">Slide Title Here</span></div>
  <div class="agenda-item" style="left:76px; top:546px;"><span class="agenda-number">04</span><span class="agenda-label">Slide Title Here</span></div>
  <div class="agenda-item" style="left:76px; top:642px;"><span class="agenda-number">05</span><span class="agenda-label">Slide Title Here</span></div>

  <div class="agenda-item right" style="left:599px; top:240px;"><span class="agenda-number">06</span><span class="agenda-label">Slide Title Here</span></div>
  <div class="agenda-item right" style="left:599px; top:336px;"><span class="agenda-number">07</span><span class="agenda-label">Slide Title Here</span></div>
  <div class="agenda-item right" style="left:599px; top:440px;"><span class="agenda-number">08</span><span class="agenda-label">Slide Title Here</span></div>
  <div class="agenda-item right" style="left:599px; top:546px;"><span class="agenda-number">09</span><span class="agenda-label">Slide Title Here</span></div>
  <div class="agenda-item right" style="left:599px; top:642px;"><span class="agenda-number">10</span><span class="agenda-label">Slide Title Here</span></div>

  <footer class="slide-footer">
    <span class="brand-name">Veranthix</span>
    <div class="presenter">
      <span class="presenter-label">Persentator Name &nbsp;:</span>
      <span class="presenter-name">Lena Moraski</span>
    </div>
  </footer>
</div>
</body>
</html>
```